Business Card Design

New business card design

Target Market(s)

Residential & Commercial Property Managers

Industry/Entity Type

Plumbing Services

Contact Information for Business Card

Name - Rowan Keddle, title - Director, Phone Number - 0431 286 517, email - rowan@tbk-plumbing.com.au, Company ABN - 73 215 904 386,

Font styles to use
Sans Serif

Colors
0054AA
0677BA
7BADD7
CADEEF
E8F1F8

```html
<!DOCTYPE html>
<html lang="en">
<head>
<meta charset="utf-8">
<title>Business Card – Rowan Keddle, Director</title>
<link rel="stylesheet" href="https://fonts.googleapis.com/css2?family=Poppins:wght@300;400;500;600&display=swap">
<style>
  :root {
    --stage: #232323;
    --card-white: #ffffff;
    --brand-blue: #26a9e0;
    --blue-deep: #0677ba;
    --blue-soft: #7badd7;
    --ink-navy: #1d2b36;
    --ink-warm: #6d6460;
    --ink-black: #1a1a1a;
  }
  * { box-sizing: border-box; margin: 0; padding: 0; }
  html, body {
    width: 1200px;
    height: 780px;
    overflow: hidden;
    background: var(--stage);
    font-family: "Poppins", sans-serif;
  }
  .card {
    position: absolute;
    top: 225px;
    width: 540px;
    height: 330px;
    overflow: hidden;
  }
  .card--front { left: 40px; background: var(--card-white); }
  .card--back { left: 620px; }

  .brand-name {
    position: absolute;
    left: 150px;
    top: 38px;
    font-size: 46px;
    font-weight: 400;
    letter-spacing: 1px;
    color: var(--ink-navy);
    line-height: 1;
  }
  .abn {
    position: absolute;
    left: 40px;
    top: 130px;
    font-size: 12px;
    font-weight: 400;
    color: var(--brand-blue);
  }
  .contact-band {
    position: absolute;
    left: 0;
    bottom: 0;
    width: 450px;
    height: 96px;
    background: var(--brand-blue);
    padding: 18px 0 0 30px;
  }
  .contact-list { list-style: none; }
  .contact-item {
    display: flex;
    align-items: center;
    gap: 9px;
    color: var(--card-white);
    font-size: 13px;
    font-weight: 400;
    line-height: 20px;
  }
  .contact-icon { width: 12px; height: 12px; flex: none; }

  .person {
    position: absolute;
    right: 40px;
    top: 172px;
    text-align: right;
  }
  .person-name { font-size: 27px; line-height: 1.1; }
  .person-first { font-weight: 600; color: var(--brand-blue); }
  .person-last { font-weight: 300; color: var(--ink-warm); }
  .person-title {
    font-size: 14px;
    font-weight: 500;
    color: var(--ink-black);
    margin-top: 2px;
  }
  .side-tab {
    position: absolute;
    right: 0;
    top: 178px;
    width: 14px;
    height: 34px;
    background: var(--brand-blue);
  }

  .back-pattern {
    position: absolute;
    inset: 0;
    background: linear-gradient(135deg, var(--blue-deep) 0%, var(--brand-blue) 45%, var(--blue-soft) 100%);
  }
</style>
</head>
<body>
  <section class="card card--front" aria-label="Business card front">
    <div class="brand-name">tbk plumbing</div>
    <p class="abn">ABN - 73 215 904 386</p>

    <div class="person">
      <p class="person-name"><span class="person-first">Rowan</span> <span class="person-last">Keddle</span></p>
      <p class="person-title">Director</p>
    </div>
    <div class="side-tab"></div>

    <div class="contact-band">
      <ul class="contact-list">
        <li class="contact-item">
          <svg class="contact-icon" viewBox="0 0 24 24" aria-hidden="true"><path fill="#fff" d="M6.6 10.8a15.1 15.1 0 0 0 6.6 6.6l2.2-2.2a1 1 0 0 1 1-.25 11.4 11.4 0 0 0 3.6.6 1 1 0 0 1 1 1V20a1 1 0 0 1-1 1A17 17 0 0 1 3 4a1 1 0 0 1 1-1h3.5a1 1 0 0 1 1 1c0 1.25.2 2.45.6 3.6a1 1 0 0 1-.25 1z"/></svg>
          <span>0431 286 517</span>
        </li>
        <li class="contact-item">
          <svg class="contact-icon" viewBox="0 0 24 24" aria-hidden="true"><circle cx="12" cy="12" r="10" fill="none" stroke="#fff" stroke-width="2"/><path d="M2 12h20M12 2c3 3 3 17 0 20M12 2c-3 3-3 17 0 20" fill="none" stroke="#fff" stroke-width="1.8"/></svg>
          <span>www.tbk-plumbing.com.au</span>
        </li>
        <li class="contact-item">
          <svg class="contact-icon" viewBox="0 0 24 24" aria-hidden="true"><rect x="2" y="5" width="20" height="14" rx="1.5" fill="none" stroke="#fff" stroke-width="2"/><path d="M2.5 6l9.5 7 9.5-7" fill="none" stroke="#fff" stroke-width="2"/></svg>
          <span>rowan@tbk-plumbing.com.au</span>
        </li>
      </ul>
    </div>
  </section>

  <section class="card card--back" aria-label="Business card back">
    <div class="back-pattern" role="img" aria-label="Repeating pattern of light and dark blue water drops covering the card"></div>
  </section>
</body>
</html>
```